Business Card for Vorla Parts Wholesale supplier

Hi There! I need a new business card for our company. We are specialized in selling Vorla parts, mostly we sell new LCD screens for Zelnar and Drelks. I would like to see that back in the design.

You can find the colors and logo's on our website: www.hartuvo.nl

Industry/Entity Type

Business

Contact Information for Business Card

My Details:
Tobias Lindqvist

Phone: 0031687203316
E-mail: Tobias@hartuvo.nl

Slogan: "Because Quality Matters"

Font styles to use
Sans Serif

Colors

Designer to choose colors to be used in the design.

Requirements
Must have
• A Black backside with the Hartuvo logo on it. The front side should be clean with only my contact details.
• But I'm also open for something really different or awesome!
Nice to have
• Remember that we are in the parts & repairing industry, So i'll be handing those business cards mainly to repair companies. Maybe you can do something with that thought :)

```html
<!DOCTYPE html>
<html lang="en">
<head>
<meta charset="utf-8">
<title>Hartuvo Business Card</title>
<link rel="stylesheet" href="https://fonts.googleapis.com/css2?family=Didact+Gothic&display=swap">
<style>
  :root {
    --stage: #2b2725;
    --card-back: #141414;
    --card-front: #1e1e1f;
    --card-front-edge: #282829;
    --accent: #f26a1b;
    --ink-light: #e9e9e9;
    --ink-muted: #c9c9c9;
    --mark-faint: #2a2a2b;
    --mark-emboss: #232323;
  }
  * { margin: 0; padding: 0; box-sizing: border-box; }
  html, body { width: 1200px; height: 715px; overflow: hidden; }
  body {
    background: var(--stage);
    font-family: "Didact Gothic", "Century Gothic", sans-serif;
    position: relative;
  }
  .card {
    position: absolute;
    width: 520px;
    height: 297px;
    top: 209px;
    border-radius: 4px;
    overflow: hidden;
    box-shadow: 0 18px 40px rgba(0,0,0,0.45);
  }
  .card--back { left: 60px; background: var(--card-back); }
  .card--front {
    left: 620px;
    background: linear-gradient(135deg, var(--card-front-edge), var(--card-front) 60%);
  }
  .back-mark {
    position: absolute;
    left: 50%; top: 50%;
    width: 120px; height: 120px;
    margin: -60px 0 0 -60px;
    border-radius: 50%;
    background: var(--mark-emboss);
    box-shadow: inset 0 2px 3px rgba(255,255,255,0.05), inset 0 -2px 4px rgba(0,0,0,0.5);
  }
  .front-mark {
    position: absolute;
    right: -60px; top: 40px;
    width: 290px; height: 290px;
    border-radius: 50%;
    border: 38px solid var(--mark-faint);
  }
  .contact {
    position: absolute;
    left: 40px; top: 34px;
    color: var(--ink-light);
  }
  .contact__name {
    color: var(--accent);
    font-size: 19px;
    font-weight: 700;
    letter-spacing: 0.3px;
  }
  .contact__role {
    font-size: 13px;
    color: var(--ink-muted);
    margin-top: 2px;
  }
  .contact__lines {
    list-style: none;
    margin-top: 22px;
    font-size: 14.5px;
    line-height: 1.35;
  }
  .brand {
    position: absolute;
    left: 40px; bottom: 42px;
    display: flex;
    align-items: center;
    gap: 12px;
  }
  .brand__dot {
    width: 40px; height: 40px;
    border-radius: 50%;
    background: var(--accent);
  }
  .brand__name {
    color: var(--ink-light);
    font-size: 46px;
    line-height: 1;
    letter-spacing: 0.5px;
  }
</style>
</head>
<body>
  <section class="card card--back" aria-label="Card back">
    <div class="back-mark" aria-hidden="true"></div>
  </section>

  <section class="card card--front" aria-label="Card front">
    <div class="front-mark" aria-hidden="true"></div>
    <div class="contact">
      <p class="contact__name">Tobias Lindqvist</p>
      <p class="contact__role">Managing Director</p>
      <ul class="contact__lines">
        <li>0031687203316</li>
        <li>Tobias@hartuvo.nl</li>
        <li>www.hartuvo.nl</li>
      </ul>
    </div>
    <div class="brand">
      <span class="brand__dot" aria-hidden="true"></span>
      <span class="brand__name">hartuvo</span>
    </div>
  </section>
</body>
</html>
```